Redesign of norbacute.com website (3 page types)

We need a fresh rebrush of www.norbacute.com, a portal for french regions, departements and cities. It shall look modern as the current design is over 10 years old.

We like the blueish colors and the french touch (blue, white, red).

There are 3 page types that we currently need:
- Homepage (http://www.norbacute.com/)
- Region overview (e.g. http://www.norbacute.com/provence-alpes-cote-d-azur)
- City overview (e.g. http://www.norbacute.com/provence-alpes-cote-d-azur/bouches-du-rhone/marseille)

See "Must have" for a more detailed briefing. All required elements exist and need a rebrush/redesign

Requirements
Must have
• General:

- 3 column layout
+ Header
+ Left sidebar
+ Content area
+ Right sidebar (250px inner width for ads)
+ Footer
- 3 classes of headlines
- Simple sidebar widgets (headline & content / without headline)

Header:
- Logo
- 2 or 3 links
- Search box
- Breadcrumb navigation

Footer:
- Nothing special, really

Homepage:
- Nice looking map with visible region borders to create a mouseover effect (as seen on current version). Meaning we need the plain map and a version with each region highlighted
- Text areas
- Content boxes (like the current gray ones)

Region overview
- Headline
- Info box (Informations)
- Mini map
- Crest / emblem
- Text area with headline for a long descriptive text with a "read more" / "show less" button/link to pop out the whole text via javascript
- List of the 24 biggest cities in the region

City overview
- Headline
- Info box (Informations, same look as for regions)
- Mini map
- List of the 24 cities nearby
- List of available photos
- Example sidebar widgets (right sidebar):
+ Upload a photo of this city
+ Weather conditions
+ Link list
Nice to have
• - A new favicon
- Chatterly og:image
Should not have
• - Flash
- Animations

```html
<!DOCTYPE html>
<html lang="fr">
<head>
<meta charset="utf-8">
<title>norbacute.com – Les villes de France</title>
<link rel="stylesheet" href="https://fonts.googleapis.com/css2?family=Open+Sans:ital,wght@0,400;0,600;0,700;1,400;1,600&display=swap">
<style>
:root{
  --page:#eef5fa;
  --navy:#2f5d85;
  --panel:#c9dff0;
  --ink:#333;
  --link:#1f4f7a;
  --red:#8e1c1c;
  --red-bright:#c0282d;
  --footer-top:#2a5076;
  --footer-bottom:#3e6a93;
  --thumb:#c8dcee;
}
*{box-sizing:border-box;margin:0;padding:0}
html,body{width:1200px;height:2980px;overflow:hidden}
body{background:var(--page);font-family:"Open Sans",sans-serif;color:var(--ink);position:relative}
a{color:inherit;text-decoration:none}
.abs{position:absolute}

/* header */
.topbar{left:0;top:0;width:1200px;height:70px;background:#fff}
.topbar-accent{left:860px;top:0;width:340px;height:70px;background:var(--red)}
.brand{left:87px;top:24px;width:176px;height:90px;background:var(--red-bright);display:flex;align-items:center;gap:10px;padding:0 16px;color:#fff;font-size:24px;font-weight:700}
.brand-mark{width:16px;height:16px;background:#fff}
.nav{left:418px;top:22px;display:flex;gap:22px;font-size:16px;color:#333}
.nav a{padding:3px 10px}
.nav a.active{background:var(--navy);color:#fff}
.search{left:918px;top:20px;width:212px;height:36px;background:#fff;border:1px solid #ddd;font-style:italic;color:#999;font-size:15px;padding:7px 12px}
.search svg{position:absolute;right:10px;top:11px}
.hero{left:0;top:70px;width:1200px;height:294px;background:linear-gradient(180deg,#7d8ea0 0%,#9fa9ae 45%,#8c6f52 100%)}
.hero-title{left:0;top:138px;width:1200px;text-align:center;color:#fff;font-size:72px;font-weight:700;letter-spacing:-1px;line-height:90px}
.hero-sub{left:0;top:230px;width:1200px;text-align:center;color:#fff;font-size:17px}

/* map */
.map{left:330px;top:290px;width:480px;height:440px;background:radial-gradient(ellipse at 50% 45%,#3b6088 0%,#3b6088 52%,rgba(238,245,250,0) 70%)}

/* sidebars */
.widget-head{background:var(--navy);color:#fff;font-weight:700;font-size:17px;padding:12px 22px;height:46px}
.widget-body{background:var(--panel);padding:12px 22px;font-size:14px;line-height:25.4px}
.widget-body li{list-style:none}
.widget-body a.current{color:var(--link);text-decoration:underline;font-weight:600}
.left-col{left:64px;top:318px;width:242px}
.left-col .widget-body{line-height:26.2px;padding:14px 22px 16px}
.right-col{left:860px;top:318px;width:274px}
.right-col .widget{margin-bottom:20px}
.random-photo{width:104px;height:64px;background:#9a8a6e;margin:14px 0 26px}

/* intro */
.intro{left:348px;top:762px;width:478px;text-align:center;font-size:14px;line-height:31px;color:#444}
.intro p{margin-bottom:22px}

/* section headings */
.section-title{left:64px;color:var(--navy);font-size:28px;font-weight:700}

/* city cards */
.card{top:1423px;width:327px}
.card-img{height:150px;background:linear-gradient(135deg,#1e3a5c,#6a8fae)}
.card h3{margin-top:22px;font-size:16px;font-weight:700;color:#333}
.card p{margin-top:6px;font-size:13.5px;line-height:27px;color:#777;height:189px;overflow:hidden}
.card p b{color:#555}
.card .more{display:block;text-align:right;font-style:italic;color:var(--link);font-size:15px;margin-top:52px}

/* news */
.news{width:520px;height:145px;display:flex;gap:27px}
.news-img{flex:none;width:147px;height:145px;background:var(--thumb)}
.news-body{position:relative;width:340px;height:145px}
.news h4{font-size:15px;font-weight:700;color:#333;line-height:20px}
.news p{font-size:13.5px;line-height:20px;color:#888;margin-top:8px;height:60px;overflow:hidden}
.news .more{position:absolute;right:0;bottom:0;font-style:italic;color:var(--link);font-size:15px}

/* footer */
.footer{left:0;top:2597px;width:1200px;height:383px;background:linear-gradient(180deg,var(--footer-top),var(--footer-bottom));color:#fff}
.f-brand{left:86px;top:30px;display:flex;align-items:center;gap:8px;font-size:24px;font-weight:700}
.f-brand span{width:14px;height:14px;background:#fff}
.f-copy{left:86px;top:106px;font-size:15px}
.f-links{left:86px;top:160px;font-size:15px;line-height:27px;list-style:none}
.f-links a.current{font-weight:700;text-decoration:underline}
.f-title{font-size:16px;letter-spacing:.5px;font-weight:400}
.f-cities{list-style:none;font-size:15px;font-weight:600;line-height:36px;margin-top:14px}
.f-cities a.current{text-decoration:underline}
.f-news h6{font-size:15px;font-weight:600;margin-top:18px;line-height:21px}
.f-news em{display:block;font-size:12px;margin-top:10px}
.f-news p{font-size:15px;line-height:21px;margin-top:12px}
.f-news .more{display:block;color:#fff;margin-top:6px;font-weight:600;font-style:italic;font-size:15px}
.thumbs{display:grid;grid-template-columns:repeat(3,66px);gap:25px 22px;margin-top:20px}
.thumbs div{height:66px}
</style>
</head>
<body>

<header>
  <div class="abs topbar"></div>
  <div class="abs hero" role="img" aria-label="Photo panoramique de Paris avec la tour Eiffel en automne"></div>
  <div class="abs topbar-accent"></div>
  <a class="abs brand" href="http://www.norbacute.com/"><span class="brand-mark"></span>norbacute</a>
  <nav class="abs nav">
    <a class="active" href="#">HOME</a><a href="#">ARCHIVES</a><a href="#">ABOUT</a><a href="#">CONTACT</a>
  </nav>
  <div class="abs search">Recherche
    <svg width="12" height="12" viewBox="0 0 12 12"><circle cx="5" cy="5" r="3.5" fill="none" stroke="#999" stroke-width="1.5"/><line x1="7.5" y1="7.5" x2="11" y2="11" stroke="#999" stroke-width="1.5"/></svg>
  </div>
  <h1 class="abs hero-title">Les villes de France</h1>
  <p class="abs hero-sub">Trouvez ici les régions, départements et villes français.</p>
</header>

<div class="abs map" role="img" aria-label="Carte des régions de France, région Provence-Alpes-Côte d'Azur mise en évidence"></div>

<aside class="abs left-col">
  <div class="widget-head">Les régions</div>
  <ul class="widget-body">
    <li><a class="current" href="#">Alsace</a></li><li>Aquitaine</li><li>Auvergne</li><li>Basse-Normandie</li><li>Bourgogne</li><li>Bretagne</li><li>Centre</li><li>Champagne-Ardenne</li><li>Corse</li><li>Franche-Comté</li><li>Haute-Normandie</li><li>Île-de-France</li><li>Languedoc-Roussillon</li><li>Limousin</li><li>Lorraine</li><li>Midi-Pyrénées</li><li>Nord-Pas-de-Calais</li><li>Pays de la Loire</li><li>Picardie</li><li>Poitou-Charentes</li><li>Provence-Alpes-Côte d'Azur</li><li>Rhône-Alpes</li>
  </ul>
</aside>

<section class="abs intro">
  <p>Vous vous trouvez sur un site web dédié à vous donner toutes les informations dont vous avez besoin: Nous vous mettons à disposition une liste complète indiquant toutes les villes et tous les villages de France avec leurs codes postaux et des informations touristiques. Vous pouvez aussi télécharger les plus jolies photos de votre ville.</p>
  <p>En plus, vous trouvez ici des annonces immobilières qui vous aident à trouver la maison de vos rêves, des locaux appropriés pour votre nouveau bureau ou un petit appartement au centre-ville.</p>
  <p>Plusieurs informations supplémentaires, comme le service de météo, la possibilité d'inscrire votre propre siteweb lié à votre ville et les actualités locaux, rendent complet le total de notre offerte gratuite.</p>
</section>

<aside class="abs right-col">
  <div class="widget">
    <div class="widget-head">La France</div>
    <ul class="widget-body"><li>Statistique</li></ul>
  </div>
  <div class="widget">
    <div class="widget-head">Les plus grandes villes</div>
    <ul class="widget-body">
      <li>Paris</li><li><a class="current" href="#">Marseille</a></li><li>Lyon</li><li>Toulouse</li><li>Nice</li><li>Nantes</li><li>Strasbourg</li><li>Montpellier</li><li>Bordeaux</li><li>Lille</li><li>Rennes</li><li>Le Havre</li><li>Reims</li><li>Saint-Étienne</li><li>Toulon</li><li>Grenoble</li><li>Angers</li><li>Dijon</li><li>Brest</li><li>Le Mans</li>
    </ul>
  </div>
  <div class="widget">
    <div class="widget-head">Photo par hasard</div>
    <div class="widget-body"><div class="random-photo" role="img" aria-label="Photo aléatoire d'une ville"></div></div>
  </div>
  <div class="widget">
    <div class="widget-head">Partenaires</div>
    <ul class="widget-body"><li><a class="current" href="#">La Suisse</a></li><li>Skiurlaub Frankreich</li></ul>
  </div>
</aside>

<h2 class="abs section-title" style="top:1352px">Les plus belles villes du mois</h2>

<article class="abs card" style="left:66px">
  <div class="card-img" role="img" aria-label="Strasbourg de nuit au bord de l'eau"></div>
  <h3>Strasbourg</h3>
  <p>La « capitale européenne » <b>Strasbourg</b> est aussi la capitale historique de l'Alsace à l'est de la France. Strasbourg compte 272 500 habitants et est aussi le chef-lieu du département Bas-Rhin. Au fil du développement de l'union européenne, Strasbourg, aussi à cause de sa situation géographique à la frontière franco-allemande,</p>
  <a class="more" href="#">Continue reading...</a>
</article>
<article class="abs card" style="left:437px">
  <div class="card-img" role="img" aria-label="Vieux port de Marseille et fort" style="background:linear-gradient(135deg,#8aa8c4,#c9b89a)"></div>
  <h3>Marseille</h3>
  <p><b>Marseille</b> n'est pas seulement la ville la plus âgée de la France - à cause de son important port commercial, elle est aussi appelée « la porte au monde ». Fondée en 600 avant J.-C. par des marins Grecs de Phocée, Marseille est le premier port de la France. Marseille est le siège d'un archevêque, ville d'université et capitale de départements Bouches-du-Rhône.</p>
  <a class="more" href="#">Continue reading...</a>
</article>
<article class="abs card" style="left:809px">
  <div class="card-img" role="img" aria-label="Village de Bormes-les-Mimosas sur la colline" style="background:linear-gradient(135deg,#9cc0e0,#8a9a6a)"></div>
  <h3>Bormes-Les-Mimosas</h3>
  <p><b>Bormes-Les-Mimosas</b> est un vieux village provençal situé sur la côte méditerranéenne au pied du massif boisé des Maures dans le département du Var. L'existence du village remonte au moins au 12ème siècle et des découvertes archéologiques permettent de penser que le peuplement s'est effectué dès l'époque celtique (vers 400 av. J.-C)...</p>
  <a class="more" href="#">Continue reading...</a>
</article>

<h2 class="abs section-title" style="top:1942px">Actualités locales</h2>

<article class="abs news" style="left:66px;top:2011px">
  <div class="news-img" role="img" aria-label="Image d'actualité"></div>
  <div class="news-body"><h4>Karim Valdari conteste l'exclusion de son allié en Iran</h4>
  <p>par Lena Vasseur DUBAI (Agence Veltra) - Le président iranien, Karim Valdari, a annoncé mercredi son intention de contester</p>
  <a class="more" href="#">Savoir plus...</a></div>
</article>
<article class="abs news" style="left:590px;top:2011px">
  <div class="news-img" role="img" aria-label="Image d'actualité"></div>
  <div class="news-body"><h4>Le sommet sur l'évasion fiscale s'ouvre, pas de décision concrète attendue</h4>
  <p>Les dirigeants européens étaient réunis mercredi pour un sommet largement consacré à la lutte contre l'évasion fiscale, qui ne devrait pourtant</p>
  <a class="more" href="#">Savoir plus...</a></div>
</article>
<article class="abs news" style="left:66px;top:2180px">
  <div class="news-img" role="img" aria-label="Image d'actualité"></div>
  <div class="news-body"><h4>Benhalla bientôt de retour en Algérie ?</h4>
  <p>Nadir Ouamrane, le ministre des Affaires étrangères, a affirmé au micro de Radio Orbe que l'état de santé du président algérien est "bon".</p>
  <a class="more" href="#">Savoir plus...</a></div>
</article>
<article class="abs news" style="left:590px;top:2180px">
  <div class="news-img" role="img" aria-label="Image d'actualité"></div>
  <div class="news-body"><h4>Russie: une Velvet Storm en grève de la faim pour protester contre le tribunal</h4>
  <p>Une jeune femme du groupe contestataire russe Velvet Storm emprisonnée a annoncé mercredi entamer une grève de la faim après avoir été</p>
  <a class="more" href="#">Savoir plus...</a></div>
</article>
<article class="abs news" style="left:66px;top:2358px">
  <div class="news-img" role="img" aria-label="Image d'actualité"></div>
  <div class="news-body"><h4>Nécessaire lutte contre l'évasion fiscale</h4>
  <p>Editorial du "Le Quotidien". Pourquoi faudrait-il prendre la mobilisation du Conseil européen contre les paradis fiscaux plus au sérieux</p>
  <a class="more" href="#">Savoir plus...</a></div>
</article>
<article class="abs news" style="left:590px;top:2358px">
  <div class="news-img" role="img" aria-label="Image d'actualité"></div>
  <div class="news-body"><h4>La Suède ébranlée par trois nuits d'émeutes à Stockholm</h4>
  <p>par Erik Lindvall et Nils Aberg STOCKHOLM (Agence Veltra) - Des centaines de jeunes ont incendié des véhicules dans des banlieues de</p>
  <a class="more" href="#">Savoir plus...</a></div>
</article>

<footer class="abs footer">
  <div class="abs f-brand"><span></span>norbacute</div>
  <p class="abs f-copy">© 2004-2013 norbacute.com</p>
  <ul class="abs f-links">
    <li><a class="current" href="#">Home</a></li><li>Archives</li><li>About</li><li>Contact</li>
  </ul>
  <div class="abs" style="left:350px;top:62px">
    <h5 class="f-title">LES PLUS BELLES VILLES</h5>
    <ul class="f-cities"><li>Strasbourg</li><li><a class="current" href="#">Marseille</a></li><li>Bormes-Les-Mimosas</li><li>Paris</li><li>Lyon</li></ul>
  </div>
  <div class="abs f-news" style="left:614px;top:62px;width:240px">
    <h5 class="f-title">LATEST NEWS</h5>
    <h6>Karim Valdari conteste l'exclusion de son allié en Iran</h6>
    <em>May 22, 2013 • 1 Comment</em>
    <p>par Lena Vasseur DUBAI (Agence Veltra) - Le président iranien, Karim Valdari, a</p>
    <a class="more" href="#">Savoir plus...</a>
  </div>
  <div class="abs" style="left:874px;top:62px">
    <h5 class="f-title">PHOTOS</h5>
    <div class="thumbs">
      <div role="img" aria-label="Photo de bâtiments" style="background:#7a8c9a"></div>
      <div role="img" aria-label="Photo de fleurs" style="background:#c0445a"></div>
      <div role="img" aria-label="Photo de cabines de plage" style="background:#d2883a"></div>
      <div role="img" aria-label="Photo de rochers" style="background:#5a4a3a"></div>
      <div role="img" aria-label="Photo de ciel" style="background:#6d8fb0"></div>
      <div role="img" aria-label="Photo de bois" style="background:#4a3a28"></div>
    </div>
  </div>
</footer>

</body>
</html>
```